Flyer Design Project

We need a flyer design for a 1 year old domestic cleaning company based in Wiltshire, England. We provide households with high quality, hard working cleaners. We would like to see designs which use blue (the colour on the logo attatched). The final design should communicate a clean, premier and thorough service in a clear and bold way. We would like the flyer to be A5 with a single sided design. We have attached an A5 word document with the words we would like to be used in the design, what we need is for you to give it some life, colour, artwork and a professional touch. We are perfectionsists which we would like to illustrate to our customer through this flyer.
Updates

payment has been guaranteed!

Sorry..... please no pictures of females on the designs. many thanks

Target Market(s)

females with higher than average income, aged 30-50. Have families and work 9-5.

Industry/Entity Type

It Company

Requirements
Must have
• The flyer must include the logo attatched and the words in the A5 document attatched. With RELIABLE CLEANERS preferably the headline. A5 - single sided.
The Flyer must also include our introductory offer.....
First Clean FREE
Allow us to demonstrate our standards

this should be emphasised.

PLEASE NOTE: can this be added to the list of words on the flyer please:

Ironing service - one day turn around
Nice to have
• some pictures - nothing cheesey. Again, pictures should communicate our modern professional approach.

```html
<!DOCTYPE html>
<html lang="en">
<head>
<meta charset="utf-8">
<title>Brookmead Cleaners – Flyer</title>
<link rel="stylesheet" href="https://fonts.googleapis.com/css2?family=Anton&family=Signika:wght@400;600;700&display=swap">
<style>
  :root {
    --bg-top: #ffffff;
    --bg-mid: #dff6fb;
    --bg-bottom: #7fd6ec;
    --ribbon-light: #7cc6f4;
    --ribbon-dark: #2f8fe0;
    --brand-blue: #2b63e4;
    --deep-navy: #0d1f5c;
    --ink: #0b1630;
    --white: #ffffff;
  }
  * { margin: 0; padding: 0; box-sizing: border-box; }
  html, body { width: 846px; height: 1200px; overflow: hidden; }
  body { font-family: "Signika", sans-serif; }

  .flyer {
    position: relative;
    width: 846px;
    height: 1200px;
    overflow: hidden;
    background: linear-gradient(180deg, var(--bg-top) 0%, var(--bg-mid) 45%, var(--bg-bottom) 100%);
  }

  /* Offer ribbon */
  .offer-ribbon {
    position: absolute;
    left: 288px;
    top: 0;
    width: 296px;
    height: 356px;
  }
  .offer-ribbon svg { position: absolute; inset: 0; }
  .offer-text {
    position: absolute;
    inset: 0;
    color: var(--white);
    text-align: left;
    padding: 38px 0 0 36px;
  }
  .offer-title {
    font-size: 34px;
    font-weight: 400;
    text-align: center;
    margin-left: -36px;
    line-height: 1;
  }
  .offer-free {
    font-size: 76px;
    font-weight: 700;
    text-align: center;
    margin-left: -36px;
    line-height: 1;
    margin-top: 6px;
    letter-spacing: 2px;
  }
  .offer-note {
    font-size: 25px;
    line-height: 1.2;
    margin-top: 22px;
  }
  .offer-phone {
    font-size: 25px;
    margin-top: 34px;
    letter-spacing: 1px;
  }

  /* Brand */
  .brand {
    position: absolute;
    top: 418px;
    left: 0;
    width: 846px;
    text-align: center;
  }
  .brand-name {
    display: inline-flex;
    align-items: center;
    gap: 12px;
    font-size: 42px;
    font-weight: 600;
    color: var(--deep-navy);
  }
  .brand-square {
    width: 40px;
    height: 40px;
    background: var(--brand-blue);
  }
  .brand-tagline {
    font-size: 17px;
    font-weight: 700;
    color: var(--ink);
    margin-top: 16px;
  }

  .headline {
    position: absolute;
    top: 562px;
    left: 0;
    width: 846px;
    text-align: center;
    font-family: "Anton", sans-serif;
    font-size: 76px;
    color: var(--brand-blue);
    letter-spacing: 1px;
    line-height: 1;
  }

  .services {
    position: absolute;
    top: 695px;
    left: 0;
    width: 846px;
    list-style: none;
    text-align: center;
    font-size: 27px;
    font-weight: 600;
    color: var(--ink);
    line-height: 44px;
  }

  .contact-pill {
    position: absolute;
    left: 262px;
    top: 1036px;
    width: 322px;
    height: 64px;
    border-radius: 32px;
    background: var(--brand-blue);
    color: var(--white);
    font-size: 16px;
    display: flex;
    align-items: center;
    justify-content: center;
    box-shadow: 0 3px 6px rgba(13, 31, 92, 0.3);
  }

  /* Photo areas */
  .photo { position: absolute; }
  .photo-supplies {
    left: 20px; top: 650px; width: 245px; height: 235px;
    border-radius: 20px;
    background: linear-gradient(160deg, #c9d2dc 0%, #8e9aa8 55%, #f2d34a 100%);
  }
  .photo-sponges {
    left: 0; top: 955px; width: 205px; height: 245px;
    background: linear-gradient(150deg, #f07a2c 0%, #9ed33a 35%, #6a4fd6 65%, #3d9ee8 100%);
    border-top-right-radius: 40px;
  }
  .photo-spray {
    left: 660px; top: 660px; width: 186px; height: 540px;
    border-top-left-radius: 60px;
    background: linear-gradient(180deg, #f4cf2a 0%, #7fc3ef 35%, #3f8fe0 100%);
  }
</style>
</head>
<body>
<main class="flyer">

  <section class="offer-ribbon">
    <svg width="296" height="356" viewBox="0 0 296 356" aria-hidden="true">
      <defs>
        <linearGradient id="ribbonFill" x1="0" y1="0" x2="0" y2="1">
          <stop offset="0" stop-color="#8ecff7"/>
          <stop offset="0.6" stop-color="#4aa3ea"/>
          <stop offset="1" stop-color="#2f8fe0"/>
        </linearGradient>
      </defs>
      <polygon points="0,0 296,0 296,356 148,300 0,356" fill="url(#ribbonFill)"/>
      <polygon points="14,0 282,0 282,330 148,282 14,330" fill="none" stroke="rgba(255,255,255,0.35)" stroke-width="2"/>
    </svg>
    <div class="offer-text">
      <p class="offer-title">First Clean</p>
      <p class="offer-free">FREE</p>
      <p class="offer-note">Allow us to demonstrate<br>our standards...</p>
      <p class="offer-phone">Tele: 07700900461</p>
    </div>
  </section>

  <header class="brand">
    <div class="brand-name"><span class="brand-square"></span>Brookmead Cleaners</div>
    <p class="brand-tagline">Premier Domestic Cleaners</p>
  </header>

  <h1 class="headline">RELIABLE CLEANERS!</h1>

  <div class="photo photo-supplies" role="img" aria-label="Bucket of cleaning supplies with brushes, sponges and yellow rubber gloves"></div>
  <div class="photo photo-sponges" role="img" aria-label="Stack of colourful cleaning sponges"></div>
  <div class="photo photo-spray" role="img" aria-label="Gloved hand holding a blue spray bottle"></div>

  <ul class="services">
    <li>Personalised Service</li>
    <li>Constantly Thorough</li>
    <li>Hassel Free</li>
    <li>Insured</li>
    <li>Regular Weekly Cleans</li>
    <li>No Contracts</li>
    <li>Ironing Service - One day turn around</li>
  </ul>

  <p class="contact-pill">Email: hello@brookmeadcleaners.co.uk</p>

</main>
</body>
</html>
```